Business Card Design for a new Senior Concierge Business 1.3.24

I need a professional business card to handout at networking events for my senior helper business. I would like to use the logo I have uploaded. The design should be clear and easy to read and should list the following information...
Delia Parkhurst
Owner
www.HarborlightElderAides.com
Cedar Hollow, Texas
936.482.5079
Delia@harborlightelderaides.com

Target Market(s)

Senior Citizens

Industry/Entity Type

Personal Helper/ Assisstant

Contact Information for Business Card

I have included the details in the project description box.

Font styles to use
Serif

Colors
0054AA
0677BA
7BADD7
CADEEF
E8F1F8
59FF00
82FF00
B8FF75
E3FFCB
F4FFEA
E54698
E96AAD
F1A4CE
F9D9EA
FCEFF6
6B429C
8869AF
B7A5CE
E3DAEB
F3F0F8

Requirements
Must have
• Include uploaded logo
Nice to have
• The log that has been uploaded
Should not have
• No crazy fonts

```html
<!DOCTYPE html>
<html lang="en">
<head>
<meta charset="utf-8">
<title>Harborlight Elder Aides – Business Card</title>
<link rel="stylesheet" href="https://fonts.googleapis.com/css2?family=Lato:wght@400;700;900&display=swap">
<style>
  :root {
    --canvas-bg: #ececef;
    --card-white: #ffffff;
    --brand-violet: #6330e8;
    --accent-red: #d9184b;
    --icon-teal: #1a9091;
    --ink: #1e1e1e;
    --divider: #7a5bd6;
  }
  * { box-sizing: border-box; margin: 0; padding: 0; }
  html, body {
    width: 1047px; height: 1200px; overflow: hidden;
    background: var(--canvas-bg);
    font-family: "Lato", Arial, sans-serif;
  }
  .canvas { position: relative; width: 1047px; height: 1200px; }
  .card {
    position: absolute; left: 156px; width: 743px; height: 424px;
    border-radius: 24px;
    box-shadow: 0 4px 14px rgba(0,0,0,0.12);
  }
  .card--front { top: 120px; background: var(--card-white); }
  .card--back { top: 634px; background: var(--brand-violet); }

  .brand {
    position: absolute; display: flex; align-items: center; gap: 12px;
    font-weight: 400; line-height: 1.0;
  }
  .brand__dot { flex: none; border-radius: 50%; }
  .brand--front {
    left: 32px; top: 213px; transform: translateY(-50%);
    color: var(--brand-violet); font-size: 38px;
  }
  .brand--front .brand__dot { width: 26px; height: 26px; background: var(--accent-red); }
  .brand--back {
    left: 0; right: 0; top: 215px; transform: translateY(-50%);
    justify-content: center;
    color: var(--card-white); font-size: 64px; gap: 24px;
  }
  .brand--back .brand__dot { width: 44px; height: 44px; background: var(--card-white); }

  .divider {
    position: absolute; left: 345px; top: 123px; width: 1px; height: 177px;
    background: var(--divider);
  }
  .contact { position: absolute; left: 371px; top: 119px; }
  .contact__name {
    font-weight: 900; font-size: 36px; color: var(--brand-violet);
    letter-spacing: 0.2px; line-height: 1.1;
  }
  .contact__role { font-size: 20px; color: var(--accent-red); margin-top: 0; }
  .contact__list { list-style: none; margin-top: 12px; }
  .contact__item {
    display: flex; align-items: center; gap: 10px;
    font-size: 19px; color: var(--ink); height: 26px;
  }
  .contact__item--phone { font-size: 21px; }
  .contact__icon { width: 18px; height: 18px; flex: none; fill: var(--icon-teal); }
</style>
</head>
<body>
<main class="canvas">
  <section class="card card--front" aria-label="Business card front">
    <div class="brand brand--front">
      <span class="brand__dot"></span>
      <span class="brand__name">Harborlight<br>Elder Aides</span>
    </div>
    <div class="divider"></div>
    <div class="contact">
      <h1 class="contact__name">DELIA PARKHURST</h1>
      <p class="contact__role">Owner</p>
      <ul class="contact__list">
        <li class="contact__item contact__item--phone">
          <svg class="contact__icon" viewBox="0 0 24 24"><path d="M6.6 10.8a15.1 15.1 0 0 0 6.6 6.6l2.2-2.2c.3-.3.7-.4 1-.2 1.1.4 2.3.6 3.6.6.6 0 1 .4 1 1V20c0 .6-.4 1-1 1A17 17 0 0 1 3 4c0-.6.4-1 1-1h3.5c.6 0 1 .4 1 1 0 1.3.2 2.5.6 3.6.1.3 0 .7-.2 1z"/></svg>
          936.482.5079
        </li>
        <li class="contact__item">
          <svg class="contact__icon" viewBox="0 0 24 24"><path d="M2 5h20v14H2V5zm2 2v.5l8 5 8-5V7H4zm0 2.9V17h16V9.9l-8 5z"/></svg>
          Delia@harborlightelderaides.com
        </li>
        <li class="contact__item">
          <svg class="contact__icon" viewBox="0 0 24 24"><path d="M12 2a10 10 0 1 0 0 20 10 10 0 0 0 0-20zm-1 17.9A8 8 0 0 1 4 12l1-.6L8 14v1a2 2 0 0 0 2 2v2.9zm6.9-2.5A2 2 0 0 0 16 16h-1v-3a1 1 0 0 0-1-1H8v-2h2a1 1 0 0 0 1-1V7h2a2 2 0 0 0 2-2v-.4a8 8 0 0 1 2.9 12.8z"/></svg>
          www.HarborlightElderAides.com
        </li>
        <li class="contact__item">
          <svg class="contact__icon" viewBox="0 0 24 24"><path d="M12 2a7 7 0 0 0-7 7c0 5.2 7 13 7 13s7-7.8 7-13a7 7 0 0 0-7-7zm0 9.5A2.5 2.5 0 1 1 12 6.5a2.5 2.5 0 0 1 0 5z"/></svg>
          Cedar Hollow, Texas
        </li>
      </ul>
    </div>
  </section>

  <section class="card card--back" aria-label="Business card back">
    <div class="brand brand--back">
      <span class="brand__dot"></span>
      <span class="brand__name">Harborlight<br>Elder Aides</span>
    </div>
  </section>
</main>
</body>
</html>
```